Business Card for Coach - ready to print

Design Business Card ready to order prints www.lukasbrenner.coach

* An Overview / Background of the Business & Services
· Coaching
· Personal growth
* The Target Market / Audience you are trying to reach
· private person in different roles (self, familiy, business role)s
* Design Specifics; any preferences or ideas for Style, Colour, Imagery, etc
· See www.lukasbrenner.coach
· "simple" design
· (small) element of surprise / unusual element

* Information that will be placed in the Business Card
· Beratung und Coaching
· Address: Lukas Brenner, Mosering 42, CH-8312 Winterthur, Mobile +41 79 264 53 07
* Do you have an existing website or Facebook page where designers can learn more about your company?
· lukasbrenner.coach

Target Market(s)

private person in different roles (self, familiy, business role)

Industry/Entity Type

Life Coaching

Contact Information for Business Card

Lukas Brenner
Mosering 42
CH-8312 Winterthur

Mobile: +41 79 264 53 07
Email: lubr@alpimail.ch
www.lukasbrenner.coach

Font styles to use
Sans Serif

Colors

Designer to choose colors to be used in the design.

Requirements
Must have
• "simple" design
• element of surprise / unusual element
• Beratung & Coaching
• see www.lukasbrenner.coach for colors and so...
Nice to have
• TA Symbol (three rings on top of each other) - unsual presentation
• QR Code of Website (see if it fits in and still looks good).

```html
<!DOCTYPE html>
<html lang="en">
<head>
<meta charset="utf-8">
<title>Business Card – Lukas Brenner Coaching</title>
<link rel="stylesheet" href="https://fonts.googleapis.com/css2?family=Lato:wght@400;700&display=swap">
<style>
  :root {
    --page-bg: #2b2b2b;
    --card-bg: #141414;
    --accent: #5bc0eb;
    --text-muted: #a2a2a2;
    --rule: #4a4a4a;
    --portrait-top: #9a9ea4;
    --portrait-bottom: #5d6570;
  }
  * { box-sizing: border-box; margin: 0; padding: 0; }
  html, body {
    width: 1200px; height: 1063px; overflow: hidden;
    background: var(--page-bg);
    font-family: "Lato", sans-serif;
  }
  .card {
    position: absolute;
    left: 250px;
    width: 700px; height: 400px;
    background: var(--card-bg);
    box-shadow: 0 18px 40px rgba(0,0,0,.55);
  }
  .card--front { top: 100px; }
  .card--back { top: 560px; }

  .portrait {
    position: absolute;
    border-radius: 50%;
    border: 2px solid var(--accent);
    background: linear-gradient(180deg, var(--portrait-top), var(--portrait-bottom));
  }
  .card--front .portrait { left: 410px; top: 28px; width: 222px; height: 222px; }
  .card--back .portrait { left: 455px; top: 28px; width: 212px; height: 212px; }

  .accent-bar {
    position: absolute; left: 28px; top: 178px;
    width: 10px; height: 58px; background: var(--accent);
  }
  .name {
    position: absolute; left: 66px; top: 140px;
    font-size: 38px; font-weight: 700; color: var(--accent);
    letter-spacing: .5px; line-height: 1;
  }
  .role {
    position: absolute; left: 68px; top: 186px;
    font-size: 18px; color: var(--text-muted);
  }
  .address {
    position: absolute; left: 84px; top: 228px;
    font-size: 19px; line-height: 25px; color: var(--text-muted);
    font-style: normal;
  }
  .address .company { color: var(--accent); }
  .contacts {
    position: absolute; left: 88px; top: 310px;
    list-style: none;
  }
  .contacts li {
    display: flex; align-items: center; gap: 18px;
    height: 28px; font-size: 18px; color: var(--text-muted);
    letter-spacing: .4px;
  }
  .contacts svg { width: 18px; height: 18px; flex: none; }

  .services-title {
    position: absolute; left: 150px; top: 212px;
    font-size: 42px; font-weight: 700; color: var(--accent); line-height: 1;
  }
  .services-rule {
    position: absolute; left: 160px; top: 268px;
    width: 220px; height: 1px; background: var(--rule);
  }
  .services-list {
    position: absolute; left: 170px; top: 278px;
    list-style: none; font-size: 29px; line-height: 36px; color: var(--text-muted);
  }
</style>
</head>
<body>

<section class="card card--front">
  <div class="portrait" role="img" aria-label="Portrait photo of the coach"></div>
  <div class="accent-bar"></div>
  <h1 class="name">JONAS KELLER</h1>
  <p class="role">Founder &amp; CEO</p>
  <address class="address">
    <span class="company">Beratung and Coaching</span><br>
    Lukas Brenner, Mosering 42<br>
    CH-8312 Winterthur
  </address>
  <ul class="contacts">
    <li>
      <svg viewBox="0 0 24 24" aria-hidden="true"><path fill="#5bc0eb" d="M6.6 10.8a15.1 15.1 0 0 0 6.6 6.6l2.2-2.2a1 1 0 0 1 1-.25 11.4 11.4 0 0 0 3.6.57 1 1 0 0 1 1 1V20a1 1 0 0 1-1 1A17 17 0 0 1 3 4a1 1 0 0 1 1-1h3.5a1 1 0 0 1 1 1c0 1.25.2 2.45.57 3.57a1 1 0 0 1-.25 1z"/></svg>
      +41 79 264 53 07
    </li>
    <li>
      <svg viewBox="0 0 24 24" aria-hidden="true"><rect x="2" y="5" width="20" height="14" fill="#5bc0eb"/><path d="M2 5l10 8 10-8" fill="none" stroke="#141414" stroke-width="1.8"/></svg>
      lubr@alpimail.ch
    </li>
    <li>
      <svg viewBox="0 0 24 24" aria-hidden="true"><circle cx="12" cy="12" r="10" fill="#5bc0eb"/><g fill="none" stroke="#141414" stroke-width="1.3"><ellipse cx="12" cy="12" rx="4" ry="10"/><path d="M2 12h20M4 7h16M4 17h16"/></g></svg>
      www.lukasbrenner.coach
    </li>
  </ul>
</section>

<section class="card card--back">
  <div class="portrait" role="img" aria-label="Portrait photo of the coach"></div>
  <h2 class="services-title">SERVIES:</h2>
  <div class="services-rule"></div>
  <ul class="services-list">
    <li>Coaching</li>
    <li>Personal growth</li>
  </ul>
</section>

</body>
</html>
```